Calder Vossik - Cinematographer

NEED:
I'm looking for a sleek, professional, modern business card that will give give the recipient the impression that they can trust their production will go smoothly by hiring me. I will bring creativity and knowledge to their shoot, so that we can create powerful images.
I am looking for a card with a strong style and design ethos that could be expanded to a website and a full visual/graphic/design entity for me.
ABOUT ME:
I am a mid-twenties cinematographer, I work on music video, narrative short, commercial, and corporate projects. I blend the science and artistry of cameras and filmmaking to tell a story. I'm an artist, a technician, and a manager.
DESIGN:
I like sleek, simple design. Black, dark grays, white, dark navy, steel blues, I love cyan, but also cyan and red. I am not a fan of earthy tones. I generally prefer modern, san-serif fonts over serifs. My old logo was based on an aperture, a multi-blade device at the back of a lens that controls how much light passes through, but I made it with so many colors, that it doesn't necessarily lend itself to a specific color-scheme or design ethos. I liked that the aperture design provided a sense of the technical requirements of my job. I'm a fan of matte business cards, but am open to plenty of specialty print processes to make an outstanding card.
ATTACHED FILES:
My Old Rainbox Aperture Logo, plus a few designs I've tried playing around with, but am not tied to. I AM OPEN TO NEW DESIGNS, DO NOT FEEL TIED TO THIS.
**I've pulled my old logo down from the attached files, and instead attached other business cards I like, so as not to mislead you where I would like to go.
INFO:
Name: Calder Vossik
Job: Cinematographer
Email: ccvossik@lumenpost.net
Phone: 415.555.0193
Website: caldervossik.com
Updates
I'm adding some images of other cards that I like, and removing my old logo, since I'm looking for something new, and don't want that old logo to push anyone a certain direction.

```html
<!DOCTYPE html>
<html lang="en">
<head>
<meta charset="utf-8">
<title>Calder Vossik – Cinematographer Business Card</title>
<link href="https://fonts.googleapis.com/css2?family=Quicksand:wght@500;600;700&display=swap" rel="stylesheet">
<style>
  :root {
    --backdrop: #e6e6e6;
    --card-dark-top: #2e2e30;
    --card-dark-bottom: #18181a;
    --paper-white: #ffffff;
    --ink-black: #141414;
    --signal-red: #e0242b;
    --text-light: #f4f4f4;
    --icon-cutout: #1e1e20;
  }
  * { margin: 0; padding: 0; box-sizing: border-box; }
  html, body {
    width: 1200px;
    height: 900px;
    overflow: hidden;
    background: var(--backdrop);
    font-family: "Quicksand", sans-serif;
  }
  .canvas {
    position: relative;
    width: 1200px;
    height: 900px;
  }
  .card {
    position: absolute;
    width: 580px;
    height: 332px;
    border-radius: 30px;
    overflow: hidden;
    box-shadow: 0 10px 30px rgba(0,0,0,0.18);
  }

  /* Front of card */
  .card-front {
    left: 70px;
    top: 90px;
    background: linear-gradient(160deg, var(--card-dark-top), var(--card-dark-bottom));
    display: flex;
    align-items: center;
    justify-content: center;
  }
  .brand-name {
    color: var(--text-light);
    font-weight: 600;
    font-size: 56px;
    letter-spacing: 0.5px;
    white-space: nowrap;
  }

  /* Back of card */
  .card-back {
    left: 550px;
    top: 470px;
    background: var(--paper-white);
  }
  .identity {
    height: 178px;
    display: flex;
    flex-direction: column;
    align-items: center;
    justify-content: center;
    color: var(--ink-black);
    text-align: center;
    line-height: 1.05;
  }
  .identity-name {
    font-weight: 700;
    font-size: 46px;
  }
  .identity-role {
    font-weight: 600;
    font-size: 34px;
  }
  .contact-band {
    position: absolute;
    left: 0; right: 0; bottom: 0;
    height: 154px;
    background: linear-gradient(180deg, var(--card-dark-top), var(--card-dark-bottom));
    border-top: 4px solid var(--signal-red);
    display: flex;
    align-items: flex-start;
    padding: 26px 20px 0 28px;
    color: var(--text-light);
    font-weight: 500;
  }
  .contact-phone {
    display: flex;
    align-items: center;
    gap: 12px;
    font-size: 23px;
    padding-top: 14px;
    white-space: nowrap;
  }
  .contact-divider {
    width: 3px;
    height: 76px;
    background: var(--signal-red);
    margin: 0 14px 0 16px;
    flex: none;
  }
  .contact-online {
    display: flex;
    flex-direction: column;
    gap: 4px;
    font-size: 21px;
  }
  .contact-line {
    display: flex;
    align-items: center;
    gap: 10px;
    white-space: nowrap;
  }
  .icon { flex: none; fill: var(--text-light); }
  .icon-detail { fill: none; stroke: var(--icon-cutout); }
</style>
</head>
<body>
<main class="canvas">

  <section class="card card-front" aria-label="Business card front">
    <span class="brand-name">Calder Vossik</span>
  </section>

  <section class="card card-back" aria-label="Business card back">
    <div class="identity">
      <h1 class="identity-name">Calder Vossik</h1>
      <p class="identity-role">Cinematographer</p>
    </div>
    <div class="contact-band">
      <div class="contact-phone">
        <svg class="icon" width="18" height="18" viewBox="0 0 24 24" aria-hidden="true">
          <path d="M6.6 10.8a15.1 15.1 0 0 0 6.6 6.6l2.2-2.2a1 1 0 0 1 1-.25 11.4 11.4 0 0 0 3.6.57 1 1 0 0 1 1 1V20a1 1 0 0 1-1 1A17 17 0 0 1 3 4a1 1 0 0 1 1-1h3.5a1 1 0 0 1 1 1c0 1.25.2 2.45.57 3.57a1 1 0 0 1-.25 1z"/>
        </svg>
        <span>415.555.0193</span>
      </div>
      <span class="contact-divider"></span>
      <div class="contact-online">
        <div class="contact-line">
          <svg class="icon" width="24" height="18" viewBox="0 0 24 18" aria-hidden="true">
            <rect x="0" y="0" width="24" height="18" rx="2"/>
            <path class="icon-detail" d="M2 2 L12 10 L22 2" stroke-width="2"/>
          </svg>
          <span>ccvossik@lumenpost.net</span>
        </div>
        <div class="contact-line">
          <svg class="icon" width="24" height="24" viewBox="0 0 24 24" aria-hidden="true">
            <circle cx="12" cy="12" r="11"/>
            <g class="icon-detail" stroke-width="1.5">
              <ellipse cx="12" cy="12" rx="5" ry="11"/>
              <line x1="1" y1="12" x2="23" y2="12"/>
              <line x1="12" y1="1" x2="12" y2="23"/>
              <path d="M3 7h18M3 17h18"/>
            </g>
          </svg>
          <span>www.caldervossik.com</span>
        </div>
      </div>
    </div>
  </section>

</main>
</body>
</html>
```